Mobile Disc Jockey Service Brochure

We are looking for a brochure to showcase our Mobile DJ Business. It needs to be something professional looking and fit our target market of Weddings. We cater to events of all types but majority of our clients are brides looking for professional service at affordable prices.

Our website for reference: http://www.theclefcart.com/
facebook for reference: https://www.facebook.com/MarcusClefCart

I've uploaded a picture of us, our logo and some other photos that might be useful. Feel free to use additional stock photos that may be applicable to our project needs. Feel free to crop photos as necessary

I'd like this to be an 8 1/2" x 11" bifold, or trifold brochure, double sided. The front can be simple with our logo and phone number. Back can also be simple with a small logo and our website. I'd like one of the areas to focus on our bio and picture, and the other areas can describe our packages and what we offer as well as our mission statement

Some other information: We provide not only Professional and Enthusiastic DJ Services but we also do Uplighting as well as Event planning.

Target Market(s)

Weddings, Anniversary Parties, Birthdays, Themed Party

Industry/Entity Type

Business

Requirements
Must have
• Something describing our services like the following (feel free to rearrange the wording if necessary).
• All packages are hourly and custom built to fit your party needs. A list of our offerings includes:
• Cocktail music, dinner music, dance music
• Ultimate coordination of activities and unique event planning experience
• HD Sound
• LED Light Show
• Wireless Microphone System
• Unlimited choice of song titles from Digital to Vinyl
• Free travel within 50 miles - Travel outside of this is calculated with a fee per additional mile.
• Optional Services:
• Projector with Screen for Slide Shows & Movies
• Uplighting
• We provide a Fun & Easy to use web interface that walks you through the timeline of your event capturing every detail you desire, making planning fun! We guarantee you will hear everything you want, we have an endless music library as well as mobile internet so we can access any song you and your guests want instantly! In addition to the Online Event Planner, we offer unlimited consultations prior to your event to ensure face to face that you are getting everything you want and more.
• I'd like to see something featuring our services as well as our picture that I uploaded maybe cropped at the chest level or there abouts with this information:
• We are a husband and wife team. Marcus Holloway, the DJ has been providing custom soundtracks for events of all types for well over a decade. In 2011 his wife Tessa joined the team to handle all of the event coordination and logistics. Together we run the Clef Cart offering Professional DJ Services at a personal level. We enjoy working with clients to create the event that they deserve at an affordable price. Contact us today for your quote or visit us online.
• (555) 314-2286
• theclefcart@mailvo.com
• www.theclefcart.com
• www.facebook.com/MarcusClefCart
• Id also like something along the lines of:
• Your choice of DJ can make or break your event. The Clef Cart guarantees to go above and beyond to make your event flawless and unforgettable. We promise to provide nothing but the best, well within your budget. When it comes to Weddings, we recognize that your Wedding is the most important day of your life! We will work with you side by side to ensure that it's everything you have dreamed of and more. Let the experience we provide create a beautiful memory that will last a lifetime.
• (Mission Statement)
• Our mission is to provide high quality and affordable mobile DJ services that will fill your event with beautiful lifelong memories.
Nice to have
• Id like to see the picture of the bride and grandfather dancing put in there somewhere.
• Color Scheme should be a mix of greys, black, white, you can add color as needed to match photos/logo, etc.

```html
<!DOCTYPE html>
<html lang="en">
<head>
<meta charset="utf-8">
<title>The Clef Cart – Mobile DJ Brochure</title>
<link rel="stylesheet" href="https://fonts.googleapis.com/css2?family=Ubuntu:wght@400;500;700&family=Open+Sans:wght@400;600;700&display=swap">
<style>
  :root {
    --red: #b5140e;
    --red-dark: #9a0f0a;
    --steel: #c6d3d6;
    --paper: #eceeee;
    --paper-light: #f4f5f5;
    --ink: #2b2b2b;
    --ink-soft: #4a4a4a;
    --white: #ffffff;
    --backdrop: #dde3e3;
  }
  * { box-sizing: border-box; margin: 0; padding: 0; }
  html, body {
    width: 1200px; height: 1000px; overflow: hidden;
    background: var(--backdrop);
  }
  .brochure {
    position: absolute; left: 50px; top: 75px;
    width: 1100px; height: 850px;
    background: var(--paper);
    overflow: hidden;
    box-shadow: 0 6px 24px rgba(0,0,0,.18);
    font-family: "Open Sans", Arial, sans-serif;
    color: var(--ink);
  }
  .brochure-shapes { position: absolute; inset: 0; }

  .heading { font-family: "Ubuntu", Arial, sans-serif; text-transform: uppercase; line-height: 1; }
  .heading .kicker { display: block; font-size: 13px; font-weight: 400; letter-spacing: .5px; }
  .heading .main { display: block; font-size: 22px; font-weight: 700; }

  /* Offerings panel */
  .offerings-title { position: absolute; left: 42px; top: 92px; color: var(--white); }
  .offerings-title .main { font-size: 24px; }
  .offering {
    position: absolute; width: 120px; text-align: center;
    font-family: "Ubuntu", Arial, sans-serif; font-weight: 700; font-size: 11px; color: var(--ink);
  }
  .offering svg { display: block; margin: 0 auto 4px; width: 36px; height: 36px; }
  .offering .led { display: block; font-size: 30px; font-weight: 700; color: var(--red); line-height: 36px; letter-spacing: 1px; margin-bottom: 4px; }
  .travel-note {
    position: absolute; left: 42px; top: 742px; width: 260px;
    font-size: 10px; line-height: 1.45; color: var(--ink-soft);
  }

  /* Middle copy */
  .mission { position: absolute; left: 385px; top: 250px; width: 225px; }
  .section-title { color: var(--ink); margin-bottom: 8px; }
  .section-title .main { font-size: 20px; }
  .mission p, .memorable p { font-size: 8.7px; line-height: 1.42; color: var(--ink-soft); margin-bottom: 6px; }
  .memorable { position: absolute; left: 385px; top: 345px; width: 205px; }

  /* Gallery */
  .gallery-title { position: absolute; left: 645px; top: 100px; color: var(--white); }
  .gallery-title .main { font-size: 21px; }
  .photo {
    position: absolute; border: 4px solid var(--white);
    box-shadow: 0 3px 8px rgba(0,0,0,.25);
  }
  .photo-bride { left: 875px; top: 95px; width: 170px; height: 215px; background: linear-gradient(160deg, #2a2430, #6b5a66 55%, #d9d2da); }
  .photo-floor { left: 640px; top: 258px; width: 172px; height: 125px; background: linear-gradient(180deg, #3b3a4a, #8a8494 60%, #cfc9cf); }
  .photo-crowd { left: 595px; top: 398px; width: 198px; height: 160px; background: linear-gradient(170deg, #1c1c26, #3c3a4a 60%, #5d5868); }
  .photo-party { left: 810px; top: 330px; width: 190px; height: 140px; background: linear-gradient(160deg, #6a5a52, #a88a80 50%, #3a2f3a); }
  .photo-lights { left: 800px; top: 487px; width: 180px; height: 108px; background: linear-gradient(135deg, #2c2a6e, #5b3c8c 40%, #2f7e6a 75%, #b4324a); }

  /* Testimonials */
  .testimonials-title { position: absolute; left: 606px; top: 582px; color: var(--ink); }
  .testimonials-title .main { font-size: 21px; }
  .testimonial { position: absolute; color: var(--white); }
  .avatar { position: absolute; width: 66px; height: 66px; border: 3px solid var(--white); box-shadow: 0 2px 6px rgba(0,0,0,.25); }
  .avatar-one { background: linear-gradient(160deg, #b9b2ba, #6a5d66); }
  .avatar-two { background: linear-gradient(160deg, #d8d4cf, #8d8076); }
  .client-name { font-family: "Ubuntu", Arial, sans-serif; font-weight: 700; font-size: 10px; }
  .client-date { font-size: 9px; opacity: .9; }
  .quote { position: absolute; font-size: 9.5px; line-height: 1.4; }
  .testimonial-one { left: 605px; top: 618px; }
  .testimonial-one .avatar { left: 0; top: 0; }
  .testimonial-one .client-meta { position: absolute; left: 0; top: 74px; width: 110px; }
  .testimonial-one .quote { left: 82px; top: 34px; width: 150px; }
  .testimonial-two { left: 850px; top: 690px; }
  .testimonial-two .avatar { left: 0; top: 0; }
  .testimonial-two .client-meta { position: absolute; left: 0; top: 74px; width: 110px; }
  .testimonial-two .quote { left: 82px; top: 4px; width: 150px; }
</style>
</head>
<body>
<main class="brochure">
  <svg class="brochure-shapes" width="1100" height="850" viewBox="0 0 1100 850" aria-hidden="true">
    <polygon points="0,0 340,0 265,850 0,850" fill="var(--steel)"/>
    <polygon points="0,230 150,230 40,850 0,850" fill="#bccacd"/>
    <polygon points="0,0 450,0 340,230 0,230" fill="var(--red)"/>
    <polygon points="750,0 1100,0 1100,650 890,650" fill="var(--steel)"/>
    <polygon points="620,0 750,0 815,300 575,230" fill="var(--red)"/>
    <polygon points="590,650 1100,650 1100,850 560,850" fill="var(--red)"/>
  </svg>

  <!-- Hero photo -->
  <svg class="brochure-shapes" width="1100" height="850" viewBox="0 0 1100 850" role="img" aria-label="Photo of a bride and groom dancing outdoors among green trees">
    <defs>
      <linearGradient id="heroTone" x1="0" y1="0" x2="0" y2="1">
        <stop offset="0" stop-color="#3f6b2c"/>
        <stop offset=".6" stop-color="#6d8a4a"/>
        <stop offset="1" stop-color="#b9b09a"/>
      </linearGradient>
    </defs>
    <polygon points="450,0 620,0 575,230 340,230" fill="url(#heroTone)" stroke="var(--white)" stroke-width="4"/>
  </svg>

  <!-- Offerings -->
  <h2 class="heading offerings-title">
    <span class="kicker">A list of our</span>
    <span class="main">Offerings</span>
    <span class="kicker">includes:</span>
  </h2>

  <div class="offering" style="left:45px; top:255px;">
    <svg viewBox="0 0 36 36"><path d="M8 4h9l-2 10a3 3 0 0 1-5 0z M12.5 15v12 M8 28h9 M19 6h9l-2 10a3 3 0 0 1-5 0z M23.5 17v11 M19 29h9" fill="none" stroke="var(--red)" stroke-width="2"/></svg>
    Cocktail music
  </div>
  <div class="offering" style="left:185px; top:290px;">
    <svg viewBox="0 0 36 36"><circle cx="18" cy="18" r="11" fill="var(--red)"/><circle cx="18" cy="18" r="6" fill="none" stroke="var(--white)" stroke-width="1.5"/><path d="M3 6v24 M33 6v24" stroke="var(--red)" stroke-width="2.5"/></svg>
    Dinner music
  </div>
  <div class="offering" style="left:45px; top:335px;">
    <svg viewBox="0 0 36 36"><path d="M14 28V9l16-4v18" fill="none" stroke="var(--red)" stroke-width="2.5"/><circle cx="10" cy="28" r="4.5" fill="var(--red)"/><circle cx="26" cy="23" r="4.5" fill="var(--red)"/></svg>
    Dance music
  </div>
  <div class="offering" style="left:185px; top:370px;">
    <svg viewBox="0 0 36 36"><rect x="5" y="7" width="26" height="24" rx="2" fill="var(--red)"/><path d="M11 4v6 M25 4v6" stroke="var(--red)" stroke-width="2.5"/><g fill="var(--white)"><rect x="9" y="15" width="4" height="4"/><rect x="16" y="15" width="4" height="4"/><rect x="23" y="15" width="4" height="4"/><rect x="9" y="22" width="4" height="4"/><rect x="16" y="22" width="4" height="4"/><rect x="23" y="22" width="4" height="4"/></g></svg>
    Event planning
  </div>
  <div class="offering" style="left:45px; top:415px;">
    <svg viewBox="0 0 36 36"><path d="M6 22v-4a12 12 0 0 1 24 0v4" fill="none" stroke="var(--red)" stroke-width="2.5"/><rect x="4" y="20" width="7" height="11" rx="2" fill="var(--red)"/><rect x="25" y="20" width="7" height="11" rx="2" fill="var(--red)"/><text x="18" y="29" text-anchor="middle" font-family="Ubuntu, sans-serif" font-weight="700" font-size="9" fill="var(--red)">HD</text></svg>
    HD Sound
  </div>
  <div class="offering" style="left:185px; top:445px;">
    <span class="led">LED</span>
    LED Light Show
  </div>
  <div class="offering" style="left:45px; top:495px;">
    <svg viewBox="0 0 36 36"><circle cx="24" cy="12" r="7" fill="var(--red)"/><path d="M19 16L6 30" stroke="var(--red)" stroke-width="4" stroke-linecap="round"/></svg>
    Wireless Microphone
  </div>
  <div class="offering" style="left:185px; top:525px;">
    <svg viewBox="0 0 36 36"><path d="M2 10h32 M2 15h32 M2 20h32 M2 25h32" stroke="var(--red)" stroke-width=".8"/><path d="M12 26V8l12-3v17" fill="none" stroke="var(--red)" stroke-width="2"/><circle cx="9.5" cy="26" r="3" fill="var(--red)"/><circle cx="21.5" cy="22" r="3" fill="var(--red)"/></svg>
    Unlimited of song
  </div>
  <div class="offering" style="left:45px; top:575px;">
    <svg viewBox="0 0 36 36"><rect x="3" y="11" width="30" height="16" rx="3" fill="var(--red)"/><circle cx="12" cy="19" r="5" fill="var(--white)"/><circle cx="12" cy="19" r="2.5" fill="var(--red)"/><rect x="21" y="16" width="8" height="2" fill="var(--white)"/><path d="M7 27v4 M29 27v4" stroke="var(--red)" stroke-width="2.5"/></svg>
    Projector with Screen
  </div>
  <div class="offering" style="left:185px; top:600px;">
    <svg viewBox="0 0 36 36"><circle cx="18" cy="20" r="12" fill="var(--red)"/><path d="M6 20h24 M18 8v24 M9 13h18 M9 27h18" stroke="var(--white)" stroke-width="1"/><path d="M18 2v6" stroke="var(--red)" stroke-width="1.5"/></svg>
    Uplighting
  </div>

  <p class="travel-note">Free travel*<br>within 50 miles - Travel outside of this is calculated with a fee per additional mile</p>

  <!-- Mission -->
  <section class="mission">
    <h2 class="heading section-title"><span class="kicker">Mission</span><span class="main">Statement</span></h2>
    <p>Our mission is to provide high quality and affordable mobile DJ services that will fill your event with beautiful lifelong memories.</p>
  </section>

  <section class="memorable">
    <h2 class="heading section-title"><span class="kicker">Make your event</span><span class="main">Memorale</span></h2>
    <p>Your choice of DJ can make or break your event. The Clef Cart guarantees to go above and beyond to make your event flawless and unforgettable. We promise to provide nothing but the best, well within your budget.</p>
    <p>When it comes to Weddings, we recognize that your Wedding is the most important day of your life! We will work with you side by side to ensure that it's everything you have dreamed of and more. Let our experience create a memory for a lifetime, you will not be disappointed!</p>
    <p>We provide a Fun &amp; Easy to use web interface that walks you through the timeline of your event capturing every detail you desire, making planning fun! We guarantee you will hear everything you want, we have an endless music library as well as mobile internet so we can access any song you and your guests want instantly!</p>
    <p>In addition to the Online Event Planner, we offer unlimited consultations prior to your event to ensure face to face that you are getting everything you want and more.</p>
  </section>

  <!-- Gallery -->
  <h2 class="heading gallery-title"><span class="kicker">Photo</span><span class="main">Gallery</span></h2>
  <div class="photo photo-bride" role="img" aria-label="Photo of a bride dancing under pink party lights"></div>
  <div class="photo photo-floor" role="img" aria-label="Photo of a bride and guests on a dance floor"></div>
  <div class="photo photo-crowd" role="img" aria-label="Photo of guests dancing in a dim reception hall"></div>
  <div class="photo photo-party" role="img" aria-label="Photo of a birthday party with balloons and DJ booth"></div>
  <div class="photo photo-lights" role="img" aria-label="Photo of colourful dance floor light patterns"></div>

  <!-- Testimonials -->
  <h2 class="heading testimonials-title"><span class="kicker">Client</span><span class="main">Testimonials</span></h2>

  <article class="testimonial testimonial-one">
    <div class="avatar avatar-one" role="img" aria-label="Photo of the client couple"></div>
    <div class="client-meta"><div class="client-name">Dorian Pike</div><div class="client-date">October 30, 2014</div></div>
    <p class="quote">Thank you guys so much for coming out. My wife and our family had tons of fun and you and your wife make a really good team! Definitely will be referring you guys because you guys have skill and good personalities!</p>
  </article>

  <article class="testimonial testimonial-two">
    <div class="avatar avatar-two" role="img" aria-label="Photo of the client"></div>
    <div class="client-meta"><div class="client-name">Celia Marsh</div><div class="client-date">June 4, 2014</div></div>
    <p class="quote">Hosted my mom party and did a great job my family was impressed . Thanks great times</p>
  </article>
</main>
</body>
</html>
```